White Paper and One-Page Advertisement for TELVORISH-QM

I need both documents to be better formatted and designed so they look professional, not something someone with mediocre word skills put together. They will go out to 1000s of industry professionals, and they need to look sharp. I need them to have my company's color palate logo, and branding on it similar to how it is now, but better. Please do not change any of the written content, but it can be arranged in any other format you think is better. Smart art and things i've already used can be omitted in favor of better designs. The developer is free to use their creativity. White paper should not be longer than the three pages unless necessary.

Target Market(s)

Life Sciences supply chain professionals

Colors
33b8a4
0592cd
9bcb3c
fbee3e
3277b5

Requirements
Must have
• Must be professional looking and not look like something done in word. Please use the color palate as seen on the documents.
Should not have
• Any changes to the written content.

```html
<!DOCTYPE html>
<html lang="en">
<head>
<meta charset="utf-8">
<title>TELVORISH-QM One-Page Advertisement</title>
<link href="https://fonts.googleapis.com/css2?family=Exo+2:wght@600;700;800&family=Open+Sans:wght@400;600;700&display=swap" rel="stylesheet">
<style>
  :root {
    --backdrop: #4a4a4a;
    --paper: #ffffff;
    --green-dark: #2a9147;
    --green-light: #76b84a;
    --teal-heading: #1d6f5a;
    --accent-green: #8cc63f;
    --body-grey: #555555;
    --photo-warm: #7a4a38;
    --photo-deep: #3c2a2a;
    --photo-teal: #2f5a62;
  }
  * { margin: 0; padding: 0; box-sizing: border-box; }
  html, body { width: 1200px; height: 2483px; overflow: hidden; }
  body { background: var(--backdrop); font-family: "Open Sans", Arial, sans-serif; position: relative; }

  .ad-page {
    position: absolute; left: 0; top: 395px;
    width: 1200px; height: 1693px;
    background: var(--paper); overflow: hidden;
  }
  .ad-shapes { position: absolute; inset: 0; }

  .brand-name {
    position: absolute; left: 55px; top: 680px; width: 412px;
    text-align: center;
    font-family: "Exo 2", Arial, sans-serif; font-weight: 800;
    font-size: 46px; color: var(--green-dark); letter-spacing: 1px;
  }

  .column { position: absolute; }
  .column-left { left: 40px; top: 950px; width: 540px; color: #fff; }
  .column-right { left: 640px; top: 950px; width: 520px; color: var(--body-grey); }

  .section-title {
    font-family: "Exo 2", Arial, sans-serif; font-weight: 800;
    font-size: 48px; letter-spacing: 1px; text-transform: uppercase;
    margin-bottom: 18px; line-height: 1.1;
  }
  .column-left .section-title { color: #fff; }
  .column-right .section-title { color: var(--teal-heading); }

  .tick-list { list-style: none; }
  .tick-list li {
    position: relative; padding-left: 34px;
    font-size: 23px; line-height: 29px; margin-bottom: 18px;
  }
  .tick-list li::before {
    content: ""; position: absolute; left: 4px; top: 6px;
    width: 9px; height: 15px;
    border-right: 3px solid currentColor; border-bottom: 3px solid currentColor;
    transform: rotate(40deg);
  }
  .column-right .tick-list li { margin-bottom: 14px; }
  .promise-title { margin-top: 26px; }

  .contact-block { position: absolute; left: 640px; top: 1508px; width: 520px; }
  .contact-title {
    font-family: "Exo 2", Arial, sans-serif; font-weight: 600;
    font-size: 50px; color: var(--teal-heading); text-transform: uppercase;
    margin-bottom: 12px; line-height: 1.1;
  }
  .contact-line {
    display: flex; align-items: center; gap: 14px;
    font-size: 25px; color: var(--body-grey); line-height: 40px;
  }
  .contact-line strong { color: var(--teal-heading); font-weight: 700; }
  .contact-icon { width: 20px; height: 20px; flex: none; }

  .white-paper-link {
    position: absolute; right: 40px; bottom: 18px;
    font-family: "Exo 2", Arial, sans-serif; font-weight: 700;
    font-size: 24px; color: var(--teal-heading); text-transform: uppercase;
  }
  .white-paper-link span { color: var(--accent-green); }
</style>
</head>
<body>
  <main class="ad-page">
    <svg class="ad-shapes" width="1200" height="1693" viewBox="0 0 1200 1693">
      <defs>
        <linearGradient id="panel-green" x1="0" y1="0" x2="1" y2="1">
          <stop offset="0" stop-color="#76b84a"/>
          <stop offset="1" stop-color="#1f8c4a"/>
        </linearGradient>
        <linearGradient id="photo-tones" x1="0" y1="0" x2="1" y2="1">
          <stop offset="0" stop-color="#3c2a2a"/>
          <stop offset="0.45" stop-color="#8a5a40"/>
          <stop offset="1" stop-color="#2f5a62"/>
        </linearGradient>
      </defs>
      <path class="green-panel" d="M0 560 L598 600 L598 1693 L0 1693 Z" fill="url(#panel-green)"/>
      <path class="photo-area" role="img" aria-label="Photograph of women in traditional dress sharing a joyful moment at a ceremony"
            d="M0 0 H1200 V845 Q1060 870 940 740 Q880 668 760 655 Q640 640 598 600 L0 545 Z" fill="url(#photo-tones)"/>
      <path d="M0 545 L598 600" stroke="#fff" stroke-width="14" fill="none"/>
      <circle class="brand-badge" cx="261" cy="714" r="214" fill="var(--green-dark)"/>
      <circle cx="261" cy="714" r="200" fill="#fff"/>
    </svg>

    <div class="brand-name">TELVORISH-QM</div>

    <section class="column column-left">
      <h2 class="section-title">Our Platform</h2>
      <ul class="tick-list">
        <li>A multi-vendor marketplace for the life science community to transact pre-market and after-market materials and equipment</li>
        <li>Researchers, manufactures, and original suppliers can create an account to buy, sell, or donate materials</li>
        <li>Part 11 compliant signature and authentication</li>
        <li>Leverages industry auditing skills to facilitate compliant and transparent transactions</li>
        <li>Some of the best and industry vendors and software used</li>
      </ul>
      <h2 class="section-title promise-title">Our Promise</h2>
      <ul class="tick-list">
        <li>A greener, more cost-efficient, and quality driven supply chain through a collaborative life sciences marketplace.</li>
      </ul>
    </section>

    <section class="column column-right">
      <h2 class="section-title">Benefits</h2>
      <ul class="tick-list">
        <li>Reduce write-offs by selling excess and obsolete materials, equipment, spare parts, etc.</li>
        <li>Buy quality materials at a reduced price.</li>
        <li>Market materials if an original supplier</li>
        <li>Donate material to researchers</li>
        <li>Acquire donated materials</li>
        <li>Collaborate and consort to reduce supply chain risk such as mutual aid agreements, joint supplier audits, etc.</li>
      </ul>
    </section>

    <section class="contact-block">
      <h2 class="contact-title">Contact Us</h2>
      <p class="contact-line">
        <svg class="contact-icon" viewBox="0 0 20 20"><circle cx="10" cy="10" r="9" fill="var(--accent-green)"/><path d="M1 10 H19 M10 1 C5 6 5 14 10 19 M10 1 C15 6 15 14 10 19" stroke="#fff" stroke-width="1.5" fill="none"/></svg>
        <span>www.<strong>telvorishqm</strong>.com</span>
      </p>
      <p class="contact-line">
        <svg class="contact-icon" viewBox="0 0 20 20"><rect x="1" y="4" width="18" height="12" rx="1" fill="var(--accent-green)"/><path d="M1 4 L10 11 L19 4" stroke="#fff" stroke-width="1.5" fill="none"/></svg>
        <span>info@<strong>telvorishqm</strong>.com</span>
      </p>
    </section>

    <p class="white-paper-link">Read our <span>White Paper</span></p>
  </main>
</body>
</html>
```